New Bicycle shop business card

Hi!
I'm looking for a business card for my new proffesional bike mechanics shop. This shop is only for fixing broken bikes and not selling bikes.
Peferbly a modern and sleek and modern design.
Colors: black, grey, red, white
Information:
Name: Rijwielwerkplaats Vanhoutte
Shop owner: Bart Vanhoutte & Marieke Segers
Website: www.rijwielwerkplaats-vanhoutte.be
Email: info@rijwielwerkplaats-vanhoutte.be
Phone number: +32471902368
Street adres: Kerkweg 46
9940 Bellebeke
Slogan/shop information: Herstellingen van alle merken.
Logo: see files.
Target Market(s)
People who seek a mechanic to fix or upgrade their bikes.
Contact Information for Business Card
Information:
Website: info@rijwielwerkplaats-vanhoutte.be
9940 Bellebeke
Logo: see files.

```html
<!DOCTYPE html>
<html lang="nl">
<head>
<meta charset="utf-8">
<title>Rijwielwerkplaats Vanhoutte – Visitekaartje</title>
<link rel="stylesheet" href="https://fonts.googleapis.com/css2?family=Montserrat:wght@700;800&family=Questrial&display=swap">
<style>
  :root {
    --stage: #2b2c2f;
    --card: #1b1c1e;
    --white: #f4f4f4;
    --silver: #c8c8ca;
    --grey: #8d8e91;
    --red: #e0203f;
  }
  * { box-sizing: border-box; margin: 0; padding: 0; }
  html, body { width: 1200px; height: 800px; overflow: hidden; }
  body {
    background: var(--stage);
    display: flex;
    align-items: center;
    justify-content: center;
    gap: 48px;
    font-family: "Questrial", "Century Gothic", sans-serif;
  }
  .card {
    width: 540px;
    height: 310px;
    background: var(--card);
    border-radius: 18px;
    position: relative;
    overflow: hidden;
    box-shadow: 0 18px 40px rgba(0,0,0,.35);
  }

  /* Front */
  .card--front {
    display: flex;
    flex-direction: column;
    align-items: center;
    justify-content: center;
    gap: 22px;
  }
  .front-mark {
    display: flex;
    align-items: center;
    gap: 14px;
  }
  .front-mark__dot {
    width: 26px;
    height: 26px;
    border-radius: 50%;
    background: var(--silver);
  }
  .front-mark__name {
    font-family: "Montserrat", sans-serif;
    font-weight: 800;
    font-size: 24px;
    letter-spacing: .02em;
    text-transform: uppercase;
    color: var(--silver);
    line-height: 1.1;
  }
  .slogan {
    color: var(--white);
    font-size: 17px;
    letter-spacing: .04em;
  }

  /* Back */
  .card--back {
    display: flex;
    align-items: center;
    padding: 0 28px;
  }
  .back-brand {
    width: 195px;
    flex: none;
    display: flex;
    flex-direction: column;
    gap: 12px;
    align-self: flex-end;
    margin-bottom: 70px;
  }
  .back-brand__dot {
    width: 28px;
    height: 28px;
    background: var(--red);
    border-radius: 4px;
  }
  .back-brand__name {
    font-family: "Montserrat", sans-serif;
    font-weight: 800;
    font-size: 15px;
    line-height: 1.2;
    color: var(--white);
    text-transform: uppercase;
    letter-spacing: .02em;
    white-space: nowrap;
  }
  .divider {
    width: 1px;
    height: 150px;
    flex: none;
    background: var(--red);
    margin: 0 18px 0 12px;
    opacity: .8;
  }
  .contact {
    color: var(--white);
    font-size: 12px;
    line-height: 1.6;
    min-width: 0;
    white-space: nowrap;
  }
  .contact__owners {
    font-family: "Montserrat", sans-serif;
    font-weight: 700;
    font-size: 11.5px;
    text-transform: uppercase;
    margin-bottom: 6px;
  }
  .contact__row { display: flex; align-items: center; gap: 8px; }
  .contact__row svg { width: 11px; height: 11px; flex: none; fill: var(--red); }
  .contact__address { margin-bottom: 4px; }
  .contact__web-domain { color: var(--red); }
</style>
</head>
<body>

<section class="card card--front" aria-label="Voorkant visitekaartje">
  <div class="front-mark">
    <span class="front-mark__dot"></span>
    <span class="front-mark__name">Rijwielwerkplaats<br>Vanhoutte</span>
  </div>
  <p class="slogan">Herstellingen van alle merken</p>
</section>

<section class="card card--back" aria-label="Achterkant visitekaartje">
  <div class="back-brand">
    <span class="back-brand__dot"></span>
    <span class="back-brand__name">Rijwielwerkplaats<br>Vanhoutte</span>
  </div>
  <span class="divider"></span>
  <div class="contact">
    <p class="contact__owners">Bart Vanhoutte &amp; Marieke Segers</p>
    <p class="contact__address">Kerkweg 46<br>9940 Bellebeke</p>
    <p class="contact__row">
      <svg viewBox="0 0 24 24" aria-hidden="true"><path d="M6.6 10.8a15.1 15.1 0 0 0 6.6 6.6l2.2-2.2a1 1 0 0 1 1-.25 11.4 11.4 0 0 0 3.6.57 1 1 0 0 1 1 1V20a1 1 0 0 1-1 1A17 17 0 0 1 3 4a1 1 0 0 1 1-1h3.5a1 1 0 0 1 1 1c0 1.25.2 2.45.57 3.57a1 1 0 0 1-.25 1z"/></svg>
      +32471902368
    </p>
    <p class="contact__row">
      <svg viewBox="0 0 24 24" aria-hidden="true"><path d="M2 5h20v14H2zm2 2v.5l8 5 8-5V7z"/></svg>
      info@rijwielwerkplaats-vanhoutte.be
    </p>
    <p class="contact__row">
      <svg viewBox="0 0 24 24" aria-hidden="true"><circle cx="12" cy="12" r="10"/></svg>
      <span>www.<span class="contact__web-domain">rijwielwerkplaats-vanhoutte.be</span></span>
    </p>
  </div>
</section>

</body>
</html>
```